National online rug retailer needs a home page design

See the FloorNest logo and create a home page design around that color theme. Details are spelled out in word document uploaded below.

Apparently this website did not take my attachement showing the logo and basic requirements.  If you would send me your email address, I will send you the attachment directly.
Best regards,
Tom Vance
tvance@mrdcorp.example

Target Market(s)

The target market is home owners 25 to 75 years old with combined incomes over $100,000 per year.

Industry/Entity Type

Online

Requirements
Must have
• Lots of white space with black letters and creative use of red and possibly one other color. Would like a compelling call to action button.

```html
<!DOCTYPE html>
<html lang="en">
<head>
<meta charset="utf-8">
<title>FloorNest.com – Home</title>
<link href="https://fonts.googleapis.com/css2?family=Open+Sans:ital,wght@0,400;0,600;0,700;1,700&display=swap" rel="stylesheet">
<style>
:root{
  --red:#d80f0f;
  --red-dark:#b50000;
  --ink:#222;
  --text:#444;
  --muted:#666;
  --line:#e3e3e3;
  --nav-top:#5a5a5a;
  --nav-bot:#3a3a3a;
  --foot-bg:#f1f1f1;
  --foot-bar:#545454;
  --white:#fff;
  --cream:#f3e9da;
}
*{box-sizing:border-box;margin:0;padding:0}
html,body{width:1073px;height:1200px;overflow:hidden;background:var(--white)}
body{font-family:"Open Sans",Arial,sans-serif;color:var(--text);position:relative}
.page{position:relative;width:1073px;height:1200px;overflow:hidden}
.abs{position:absolute}

/* header */
.brand{left:89px;top:24px;display:flex;align-items:center;gap:8px}
.brand-mark{width:22px;height:22px;background:var(--red)}
.brand-name{font-size:34px;font-weight:600;color:var(--red);letter-spacing:-.5px;line-height:1}
.brand-tag{left:167px;top:74px;font-size:10px;color:var(--muted)}
.search{left:363px;top:33px;width:360px;height:43px;border:1px solid #ddd;display:flex}
.search input{flex:1;border:0;padding:0 12px;font:italic 12px "Open Sans",sans-serif;color:#aaa;outline:none}
.search button{width:44px;border:0;background:#3c3c3c;display:flex;align-items:center;justify-content:center}
.cart{right:90px;top:19px;font-size:11px;color:var(--muted)}
.cart .count{background:#333;color:#fff;padding:0 3px}
.cart span.sep{margin:0 4px;color:#ccc}
.phone{right:90px;top:43px;font-size:16px;font-weight:700;color:var(--red)}
.account{right:90px;top:73px;font-size:11px;color:var(--muted);display:flex;align-items:center;gap:8px}
.live{background:var(--red);color:#fff;padding:2px 5px}
.online{font-weight:700;color:#555;display:flex;align-items:center;gap:4px}

/* nav */
.nav{left:0;top:110px;width:1073px;height:40px;background:linear-gradient(var(--nav-top),var(--nav-bot))}
.nav ul{list-style:none;display:flex;margin-left:89px;width:894px;height:40px;border-left:1px solid #2c2c2c}
.nav li{flex:1;display:flex;align-items:center;justify-content:center;color:#fff;font-size:13px;font-weight:600;border-right:1px solid #2c2c2c}
.nav li.active{background:#2f2f2f}

/* sidebar */
.box-title{background:var(--red);color:#fff;font-size:18px;font-weight:700;padding:0 11px;height:37px;line-height:33px;border:2px solid #fff;outline:1px solid var(--red);white-space:nowrap}
.browse{left:89px;top:164px;width:167px}
.filters{list-style:none;margin-top:9px;border:1px solid var(--line)}
.filters li{height:39px;display:flex;align-items:center;justify-content:space-between;padding:0 11px;font-size:12px;font-weight:700;color:#333;border-bottom:1px solid var(--line)}
.filters li:last-child{border-bottom:0}
.filters li b{font-size:10px;color:#888}
.testimonials{left:89px;top:541px;width:167px}
.quote{font-size:11.5px;line-height:16px;color:var(--text);margin-top:12px}
.quote + .who{font-size:12.5px;font-weight:700;font-style:italic;color:#333;margin:7px 0 0 2px}
.divider{height:1px;background:var(--line);margin:18px 0 0}
.more{display:inline-block;float:right;background:var(--red);color:#fff;font-size:12px;font-weight:700;padding:1px 11px;margin-top:-3px}

/* hero */
.hero{left:271px;top:164px;width:712px;height:312px;
  background:
    linear-gradient(90deg,rgba(246,238,226,.95) 0%,rgba(246,238,226,.85) 45%,rgba(246,238,226,0) 70%) 0 100%/100% 96px no-repeat,
    linear-gradient(180deg,#b69a7e 0%,#6b3f2a 28%,#e4d5bd 52%,#c8452e 78%,#b8301e 100%)}
.hero h1{position:absolute;left:12px;bottom:12px;font-size:28px;line-height:30px;font-weight:700;color:var(--red)}

/* featured */
.feat-title{left:273px;top:490px;width:518px;height:37px;background:linear-gradient(#555,#333);color:#fff;font-size:18px;font-weight:700;line-height:37px;padding-left:11px}
.grid{left:273px;top:527px;width:518px;height:376px;display:grid;grid-template-columns:repeat(3,1fr);grid-template-rows:repeat(2,1fr);border:1px solid var(--line);border-top:0}
.cell{border-right:1px solid var(--line);border-bottom:1px solid var(--line);display:flex;flex-direction:column;align-items:center;padding-top:18px}
.cell:nth-child(3n){border-right:0}
.cell:nth-child(n+4){border-bottom:0}
.thumb{width:132px;height:132px;border:1px solid #ccc}
.cell p{font-size:14.5px;color:#555;margin-top:10px}
.also-title{left:807px;top:490px;width:177px;font-size:17px;padding:0 9px}
.also{left:807px;top:527px;width:177px;height:376px;border:1px solid var(--line);border-top:0;padding:18px 9px 0}
.also .pic{width:159px;height:102px;border:1px solid #ccc;margin-bottom:16px}

/* footer */
.footer{left:0;top:929px;width:1073px;height:218px;background:var(--foot-bg);border-top:1px solid #e6e6e6}
.col{position:absolute;top:24px}
.col h3{font-size:14px;font-weight:700;color:var(--red);margin-bottom:5px}
.col ul{list-style:none}
.col li{font-size:11px;line-height:16px;color:#555}
.social{position:absolute;right:90px;top:48px;display:flex;gap:8px}
.social i{width:30px;height:30px;background:#1f5fa8;display:block}
.pay{position:absolute;right:90px;top:104px;display:flex;gap:5px;align-items:center}
.pay i{display:block;width:28px;height:18px;background:#d9dbe2;border:1px solid #bbb}
.pay .wide{width:110px;height:30px;background:#e2e6ee;border:0}
.badges{position:absolute;right:90px;top:150px;display:flex;gap:6px;align-items:center}
.badges .round{width:44px;height:44px;border-radius:50%;background:#d4c25a}
.badges .sq{width:60px;height:30px;background:#dcdcdc}
.copy{left:0;top:1147px;width:1073px;height:53px;background:var(--foot-bar);color:#ddd;font-size:12px;padding:19px 0 0 115px}
</style>
</head>
<body>
<div class="page">

  <div class="abs brand"><i class="brand-mark"></i><span class="brand-name">FloorNest.com</span></div>
  <div class="abs brand-tag">for domestic and heirloom values</div>

  <form class="abs search">
    <input type="text" value="Enter your search here..." aria-label="Search">
    <button type="button" aria-label="Search">
      <svg width="18" height="18" viewBox="0 0 18 18"><circle cx="7.5" cy="7.5" r="5.5" fill="none" stroke="#fff" stroke-width="2.2"/><line x1="11.5" y1="11.5" x2="16" y2="16" stroke="#fff" stroke-width="2.4" stroke-linecap="round"/></svg>
    </button>
  </form>

  <div class="abs cart">Items: <span class="count">0</span><span class="sep">|</span>Total $0.00<span class="sep">|</span>View Cart<span class="sep">|</span>Checkout</div>
  <div class="abs phone">Order toll-free: 1-888-555-0142</div>
  <div class="abs account">
    <span>My Account</span><span>Sign In</span><span class="live">Live Chat</span>
    <span class="online"><svg width="11" height="11" viewBox="0 0 11 11"><circle cx="5.5" cy="3.2" r="2.6" fill="#d80f0f"/><path d="M0.5 11 C1 7 10 7 10.5 11Z" fill="#d80f0f"/></svg>Online</span>
  </div>

  <nav class="abs nav">
    <ul>
      <li class="active">Home</li><li>Selection guides</li><li>Rug Care</li><li>FAQ</li><li>Return Policy</li><li>Free Shipping</li><li>Clearance Rugs</li>
    </ul>
  </nav>

  <aside class="abs browse">
    <div class="box-title">Browse</div>
    <ul class="filters">
      <li>RUG THEME <b>+</b></li><li>COLOR WAY <b>+</b></li><li>SIZE <b>+</b></li><li>SHAPE <b>+</b></li>
      <li>FIBER CONTENT <b>+</b></li><li>MFGR. BRAND <b>+</b></li><li>MFGR.COLLECTION <b>+</b></li><li>PRICE <b>+</b></li>
    </ul>
  </aside>

  <aside class="abs testimonials">
    <div class="box-title">Testimonials</div>
    <p class="quote">Le Lorem Ipsum est simplement du faux texte employé dans la composition et la mise en page avant impression. Le Lorem Ipsum est le faux texte standard de l'imprimerie depuis les.</p>
    <p class="who">Dana Whitfield</p>
    <div class="divider"></div>
    <p class="quote">On sait depuis longtemps que travailler avec du texte lisible et contenant du sens est source de distractions, et empêche de se concentrer sur la mise en page elle-même. L'avantage du Lorem Ipsum.</p>
    <p class="who">Lena Marsh</p>
    <span class="more">More</span>
  </aside>

  <section class="abs hero" role="img" aria-label="Photo of stacked shag and woven rugs in cream, brown and red">
    <h1>For Domestic<br>and Heirloom values</h1>
  </section>

  <div class="abs feat-title">Fuatured Rugs</div>
  <div class="abs grid">
    <div class="cell"><div class="thumb" role="img" aria-label="Persian rug" style="background:linear-gradient(135deg,#7a2a12,#c8902c)"></div><p>Persian Rugs</p></div>
    <div class="cell"><div class="thumb" role="img" aria-label="Modern rug with circles" style="background:linear-gradient(135deg,#2a221e,#5b4a3a)"></div><p>Modern Rugs</p></div>
    <div class="cell"><div class="thumb" role="img" aria-label="Ziegler rug in a room" style="background:linear-gradient(135deg,#d9d2c6,#a88d6c)"></div><p>Ziegler Rugs</p></div>
    <div class="cell"><div class="thumb" role="img" aria-label="Oriental rug in a dining room" style="background:linear-gradient(135deg,#8a6a48,#7a2c1c)"></div><p>Oriental Rugs</p></div>
    <div class="cell"><div class="thumb" role="img" aria-label="Kilim rug in a bedroom" style="background:linear-gradient(135deg,#b48a6e,#5a2a20)"></div><p>kilim Rugs</p></div>
    <div class="cell"><div class="thumb" role="img" aria-label="Shag rug in a living room" style="background:linear-gradient(135deg,#e6e2dc,#9a2a28)"></div><p>Shag Rugs</p></div>
  </div>

  <div class="abs also-title box-title">You may also like</div>
  <div class="abs also">
    <div class="pic" role="img" aria-label="Pink and grey shag rugs" style="background:linear-gradient(160deg,#7a746c,#e0306a)"></div>
    <div class="pic" role="img" aria-label="Rolled patterned rugs" style="background:linear-gradient(135deg,#3a5a3a,#c0541e,#1e2a40)"></div>
    <div class="pic" role="img" aria-label="Traditional patterned rugs" style="background:linear-gradient(135deg,#6a2a18,#c8a078)"></div>
  </div>

  <footer class="abs footer">
    <div class="col" style="left:115px">
      <h3>Customer Service</h3>
      <ul><li>Shipping</li><li>Return Policy</li><li>Privacy Policy</li><li>Ordering &amp; Delivery</li><li>Checklist</li><li>Terms of Use</li><li>Terms of Sale</li><li>Contact Us</li><li>Environmental Policy</li></ul>
    </div>
    <div class="col" style="left:349px">
      <h3>Resources</h3>
      <ul><li>Product Articles</li><li>Learning Center</li><li>Help</li><li>Refer A Friend</li><li>FloorNest Blog</li><li>Room Scene Viewer</li><li>Site Map</li><li>FAQ</li><li>Customer Testimonials</li><li>Photo Gallery</li></ul>
    </div>
    <div class="col" style="left:575px">
      <h3>Corporate Info</h3>
      <ul><li>About FloorNest.com</li><li>Careers</li><li>Affiliates</li></ul>
    </div>
    <div class="social"><i></i><i style="background:#3aa0e0"></i><i></i></div>
    <div class="pay"><i></i><i></i><i></i><i></i><i></i><i class="wide"></i></div>
    <div class="badges"><i class="round"></i><i class="round"></i><i class="sq"></i><i class="sq"></i><i class="sq"></i></div>
  </footer>

  <div class="abs copy">© Copyrights 2013 All rights Reserved</div>
</div>
</body>
</html>
```